Business Card Design

Business Card for professional consulting firm working with large financial institutions.

Target Market(s)

Executive buyers

Industry/Entity Type

Banking

Contact Information for Business Card

Mild creativity wanted. Not boring, but do elaborate artwork.

Font styles to use
Serif
Sans Serif

Colors

Designer to choose colors to be used in the design.

Requirements
Must have
• Standard business card features - company name, individual name, telephone, website, email, locations.
Nice to have
• Two colors
Should not have
• too many colors, fancy printing, cartoons.

```html
<!DOCTYPE html>
<html lang="en">
<head>
<meta charset="utf-8">
<title>m4advisory — Business Card</title>
<link rel="stylesheet" href="https://fonts.googleapis.com/css2?family=Roboto:wght@400;500;700&display=swap">
<style>
  :root {
    --backdrop: #e9e6e1;
    --card-white: #f3f3f3;
    --ink-black: #050505;
    --band-grey: #ababab;
    --back-dark: #1b1c1e;
    --back-band: #c4c4c4;
    --text-dark: #111111;
    --text-mid: #555555;
    --text-soft: #a2a2a2;
    --divider: #c9c9c9;
    --white: #ffffff;
  }
  * { margin: 0; padding: 0; box-sizing: border-box; }
  html, body { width: 1200px; height: 960px; overflow: hidden; }
  body {
    background: var(--backdrop);
    font-family: "Roboto", Arial, sans-serif;
    position: relative;
  }
  .card {
    position: absolute;
    width: 600px;
    height: 344px;
    box-shadow: 0 3px 8px rgba(0,0,0,0.25);
    overflow: hidden;
  }
  .card-front { left: 314px; top: 113px; background: var(--card-white); }
  .card-back { left: 311px; top: 472px; height: 343px; background: var(--back-dark); }

  .front-shapes { position: absolute; inset: 0; }
  .front-shapes .wedge-top { fill: var(--ink-black); }
  .front-shapes .wedge-bottom { fill: var(--band-grey); }

  .brand-name {
    position: absolute;
    font-weight: 400;
    letter-spacing: 0.01em;
    white-space: nowrap;
  }
  .card-front .brand-name {
    left: 40px; top: 150px;
    width: 260px; text-align: center;
    font-size: 31px;
    color: var(--text-dark);
  }
  .divider {
    position: absolute;
    left: 335px; top: 92px;
    width: 1px; height: 162px;
    background: var(--divider);
  }
  .contact { position: absolute; left: 365px; top: 92px; }
  .person-name {
    font-size: 20px; font-weight: 700;
    color: var(--text-dark); line-height: 24px;
  }
  .person-title {
    font-size: 15px; font-weight: 500;
    color: var(--text-soft); line-height: 18px;
    margin-bottom: 14px;
  }
  .address { font-size: 14.5px; color: var(--text-mid); line-height: 18px; margin-bottom: 10px; }
  .lines { list-style: none; }
  .lines li {
    display: flex; align-items: center; gap: 8px;
    font-size: 14.5px; color: var(--text-mid); line-height: 19.5px;
  }
  .lines svg { width: 13px; height: 13px; fill: var(--text-dark); flex: none; }

  .card-back .brand-name {
    left: 0; right: 0; top: 140px;
    text-align: center;
    font-size: 38px;
    color: var(--white);
  }
  .web-band {
    position: absolute;
    left: 0; top: 275px;
    width: 100%; height: 29px;
    background: var(--back-band);
    color: var(--white);
    font-size: 14px;
    letter-spacing: 0.55em;
    text-align: center;
    line-height: 29px;
  }
</style>
</head>
<body>
  <section class="card card-front" aria-label="Business card front">
    <svg class="front-shapes" viewBox="0 0 600 344" width="600" height="344" aria-hidden="true">
      <polygon class="wedge-top" points="0,0 600,0 0,62"/>
      <polygon class="wedge-bottom" points="600,280 600,344 0,344"/>
    </svg>
    <div class="brand-name">m4advisory</div>
    <div class="divider"></div>
    <div class="contact">
      <div class="person-name">DANIEL HART</div>
      <div class="person-title">CEO/FOUNDER</div>
      <p class="address">2140 Alder Court<br>Juneau, Alaska 99801</p>
      <ul class="lines">
        <li>
          <svg viewBox="0 0 24 24" aria-hidden="true"><path d="M6.6 10.8a15.1 15.1 0 0 0 6.6 6.6l2.2-2.2c.3-.3.7-.4 1-.2 1.1.4 2.3.6 3.6.6.6 0 1 .4 1 1V20c0 .6-.4 1-1 1A17 17 0 0 1 3 4c0-.6.4-1 1-1h3.5c.6 0 1 .4 1 1 0 1.3.2 2.5.6 3.6.1.3 0 .7-.2 1z"/></svg>
          555 214 7093
        </li>
        <li>
          <svg viewBox="0 0 24 24" aria-hidden="true"><path d="M2 5h20v14H2z M3.5 6.5 12 13l8.5-6.5" fill="none" stroke="#111" stroke-width="0"/><path d="M2 5h20v2l-10 7L2 7z"/><path d="M2 9l10 7 10-7v10H2z"/></svg>
          info@m4advisory.com
        </li>
        <li>
          <svg viewBox="0 0 24 24" aria-hidden="true"><circle cx="12" cy="12" r="10"/><path d="M2 12h20M12 2c3 3 3 17 0 20M12 2c-3 3-3 17 0 20" fill="none" stroke="#f3f3f3" stroke-width="1.5"/></svg>
          www.m4advisory.com
        </li>
      </ul>
    </div>
  </section>

  <section class="card card-back" aria-label="Business card back">
    <div class="brand-name">m4advisory</div>
    <div class="web-band">www.m4advisory.com</div>
  </section>
</body>
</html>
```